Tessmar Fahrwerkstatt
Sehr angenehme zusammenarbeit nicht aufdringlich und genau auf die Wünsche eingegangen. Wir werde sicher noch mehr zusammen Arbeiten. Gruss Lukas Hegemann Inhaber Tessmar Fahrwerkstatt
Zielgruppe
Dinks und Kunden mit viel Erfolg und hohem Ausgabepotential.
Aufgabenstellung
Unsere Firma vertreibt Fahrzeuge im Luxusbereich hauptgebiet Valmerra aber auch andere Sportwagen. Was uns fehlt ist ein optischer Wiedererkennugswert. Deshalb hätten wir gerne ein Visitenkarten Design und Briefpapier Design. Später soll auch noch eine Webseite mit gleichem Wiedererkennungswert entstehen. " Roter Faden "

```html
<!DOCTYPE html>
<html lang="de">
<head>
<meta charset="utf-8">
<title>Tessmar Fahrwerkstatt – Visitenkarte</title>
<link rel="stylesheet" href="https://fonts.googleapis.com/css2?family=Didact+Gothic&display=swap">
<style>
  :root {
    --stage: #e9e6e1;
    --navy-deep: #0f1a4a;
    --navy-mid: #26366f;
    --card-white: #ffffff;
    --ink: #111111;
    --band-text: #b9c0dc;
    --card-shadow: rgba(0, 0, 0, 0.28);
  }
  * { box-sizing: border-box; margin: 0; padding: 0; }
  html, body {
    width: 1200px;
    height: 800px;
    overflow: hidden;
    background: var(--stage);
    font-family: "Didact Gothic", "Helvetica Neue", Arial, sans-serif;
  }
  .stage {
    width: 1200px;
    height: 800px;
    display: flex;
    align-items: center;
    justify-content: center;
    gap: 60px;
  }
  .card {
    width: 510px;
    height: 330px;
    position: relative;
    overflow: hidden;
    box-shadow: 0 10px 28px var(--card-shadow);
  }

  /* Rückseite */
  .card--back {
    background: radial-gradient(ellipse at 45% 40%, var(--navy-mid) 0%, var(--navy-deep) 75%);
  }

  /* Vorderseite */
  .card--front {
    background: var(--card-white);
    display: flex;
    flex-direction: column;
  }
  .front__brand {
    flex: 0 0 232px;
    display: flex;
    align-items: center;
    justify-content: center;
    gap: 22px;
    padding-left: 20px;
  }
  .brand__dot {
    width: 58px;
    height: 58px;
    border-radius: 50%;
    background: var(--ink);
  }
  .brand__name {
    color: var(--ink);
    font-weight: 400;
    line-height: 1;
  }
  .brand__name-main {
    display: block;
    font-size: 38px;
    letter-spacing: 1px;
  }
  .brand__name-sub {
    display: block;
    font-size: 15px;
    letter-spacing: 6.2px;
    margin-top: 6px;
  }
  .front__contact {
    flex: 1;
    background: linear-gradient(180deg, var(--navy-mid) 0%, var(--navy-deep) 100%);
    color: var(--band-text);
    font-size: 11.5px;
    line-height: 1.65;
    padding: 16px 22px;
  }
  .contact__role { margin-bottom: 4px; }
</style>
</head>
<body>
  <main class="stage">
    <section class="card card--back" aria-label="Kartenrückseite"></section>

    <section class="card card--front" aria-label="Kartenvorderseite">
      <div class="front__brand">
        <span class="brand__dot" aria-hidden="true"></span>
        <p class="brand__name">
          <span class="brand__name-main">TESSMAR</span>
          <span class="brand__name-sub">FAHRWERKSTATT</span>
        </p>
      </div>
      <div class="front__contact">
        <p class="contact__role">Marlene Hofstetter | Geschäftsführerin</p>
        <p>Lindenweg 12 | 43210 Ravensfeld | Tel.: +49 (0)30 5550123</p>
        <p>Mobil: +49 (0)170 5550456 | Fax: +49 (0)30 5550789 | E-Mail: info@tessmar.de</p>
      </div>
    </section>
  </main>
</body>
</html>
```